Harborline Auto LLC

Car Dealer Customer Service
Address: 2874 Cresthaven Road, Lindenvale, KS 66999
web: www.harborlineautoxq.net
email: harborlineautoxq@mailnest.example
Phone: (931) 555-0148
Phone: (629) 555-0173

```html
<!DOCTYPE html>
<html lang="en">
<head>
<meta charset="utf-8">
<title>Harborline Auto – Business Card</title>
<link href="https://fonts.googleapis.com/css2?family=Montserrat:wght@800&family=Poppins:ital,wght@0,400;0,600;1,400&display=swap" rel="stylesheet">
<style>
  :root{
    --backdrop:#2a2a2c;
    --card:#232427;
    --card-front:#26272a;
    --blue:#1b78ad;
    --blue-bright:#2a8fd0;
    --gold:#e2a93a;
    --ink-light:#e8e8ea;
    --ink-dark:#17181a;
    --mark:#1a1b1d;
  }
  *{margin:0;padding:0;box-sizing:border-box}
  html,body{width:1200px;height:1138px;overflow:hidden;background:var(--backdrop)}
  .canvas{position:relative;width:1200px;height:1138px}
  .card{position:absolute;border-radius:14px;overflow:hidden}

  /* front */
  .card-front{left:274px;top:186px;width:622px;height:374px;background:var(--card-front)}
  .front-mark{position:absolute;left:0;right:0;top:140px;display:flex;align-items:center;justify-content:center;gap:14px}
  .front-mark .dot{width:26px;height:26px;border-radius:50%;background:var(--mark)}
  .front-mark .name{font-family:'Poppins',sans-serif;font-weight:600;font-size:34px;color:var(--mark)}
  .front-web{position:absolute;left:0;right:0;top:333px;display:flex;align-items:center;justify-content:center;gap:22px}
  .front-web .rule{width:54px;height:2px;background:var(--gold)}
  .front-web .url{font-family:'Poppins',sans-serif;font-size:15px;color:var(--ink-light)}

  /* back */
  .card-back{left:276px;top:608px;width:618px;height:374px;background:var(--card)}
  .title{position:absolute;left:26px;top:40px;font-family:'Montserrat',sans-serif;font-weight:800;font-size:37px;letter-spacing:.5px;color:var(--blue-bright)}
  .band-blue{position:absolute;left:0;right:0;top:118px;height:138px;background:var(--blue)}
  .band-gold{position:absolute;left:0;right:0;top:256px;height:62px;background:var(--gold)}
  .tagline{position:absolute;left:27px;top:142px;font-family:'Poppins',sans-serif;font-style:italic;font-size:16px;color:var(--ink-light)}
  .phone{position:absolute;left:27px;display:flex;align-items:center;gap:12px;font-family:'Poppins',sans-serif;font-weight:600;font-size:21px;letter-spacing:1px;color:#fff}
  .phone svg{width:20px;height:18px}
  .phone-1{top:175px}
  .phone-2{top:204px}
  .contact{position:absolute;left:27px;display:flex;align-items:center;gap:14px;font-family:'Poppins',sans-serif;font-size:15px;color:var(--ink-dark)}
  .contact svg{width:15px;height:14px}
  .contact-web{top:264px}
  .contact-mail{top:286px}
  .address{position:absolute;left:27px;top:327px;font-family:'Poppins',sans-serif;font-size:16px;color:var(--ink-light)}
  .badge{position:absolute;left:360px;top:116px;width:208px;height:208px;border-radius:50%;background:var(--blue-bright);display:flex;align-items:center;justify-content:center;text-align:center}
  .badge .name{font-family:'Poppins',sans-serif;font-weight:600;font-size:24px;line-height:1.15;color:var(--ink-dark)}
</style>
</head>
<body>
<div class="canvas">

  <section class="card card-front">
    <div class="front-mark">
      <span class="dot"></span>
      <span class="name">Harborline Auto</span>
    </div>
    <div class="front-web">
      <span class="rule"></span>
      <span class="url">www.harborlineautoxq.net</span>
      <span class="rule"></span>
    </div>
  </section>

  <section class="card card-back">
    <h1 class="title">HARBORLINE AUTO</h1>
    <div class="band-blue"></div>
    <div class="band-gold"></div>

    <p class="tagline">Car Dealer Customer Service</p>
    <p class="phone phone-1">
      <svg viewBox="0 0 20 18"><path fill="#e2a93a" d="M2 6c0-3 4-4 8-4s8 1 8 4l-3 1-1-2H6L5 7zM5 8h10l3 8H2z"/><circle cx="10" cy="12" r="2.4" fill="#1b78ad"/></svg>
      931-555-0148
    </p>
    <p class="phone phone-2">
      <svg viewBox="0 0 20 18"><path fill="#e2a93a" d="M2 6c0-3 4-4 8-4s8 1 8 4l-3 1-1-2H6L5 7zM5 8h10l3 8H2z"/><circle cx="10" cy="12" r="2.4" fill="#1b78ad"/></svg>
      629-555-0173
    </p>

    <p class="contact contact-web">
      <svg viewBox="0 0 15 14"><rect x="1" y="2" width="13" height="10" fill="#17181a"/><path d="M1.5 2.5l6 5 6-5" fill="none" stroke="#e2a93a" stroke-width="1.3"/></svg>
      www.harborlineautoxq.net
    </p>
    <p class="contact contact-mail">
      <svg viewBox="0 0 14 14"><circle cx="7" cy="7" r="6" fill="none" stroke="#17181a" stroke-width="1.4"/><ellipse cx="7" cy="7" rx="2.6" ry="6" fill="none" stroke="#17181a" stroke-width="1.2"/><path d="M1 7h12" stroke="#17181a" stroke-width="1.2"/></svg>
      harborlineautoxq@mailnest.example
    </p>

    <div class="badge"><span class="name">Harborline<br>Auto</span></div>

    <p class="address">2874 Cresthaven Road, Lindenvale, KS 66999</p>
  </section>

</div>
</body>
</html>
```